Simple and Clean business card design

We would like the design to be simple clean and to incorporate our colors.

We are open to your design and talent, we have the dots in our logo as we think of it as data points and we connect data points for people.

We are open to see the great creative and clean design you bring to the table

Contact Information for Business Card

please include: name, position, email, phone and website

Font styles to use
Sans Serif

Requirements
Must have
• my colors incorporated, simplicity
Nice to have
• lots of white space, simplicity
Should not have
• complexicity/ complex art

```html
<!DOCTYPE html>
<html lang="en">
<head>
<meta charset="utf-8">
<title>Nectara Business Card</title>
<link href="https://fonts.googleapis.com/css2?family=Poppins:wght@400;600;700&display=swap" rel="stylesheet">
<style>
  :root {
    --backdrop: #e6e7ea;
    --card-dark: #000000;
    --card-light: #ffffff;
    --ink: #111111;
    --brand-blue: #5b87c5;
    --brand-green: #34a853;
    --brand-yellow: #f6c026;
    --brand-red: #e8493b;
    --rule: #222222;
  }
  * { box-sizing: border-box; margin: 0; padding: 0; }
  html, body {
    width: 1200px;
    height: 900px;
    overflow: hidden;
    background: var(--backdrop);
    font-family: "Poppins", sans-serif;
  }
  .sheet {
    width: 1200px;
    height: 900px;
    display: flex;
    flex-direction: column;
    align-items: center;
    justify-content: center;
    gap: 40px;
  }
  .card {
    width: 630px;
    height: 360px;
    border-radius: 18px;
    box-shadow: 0 10px 24px rgba(0,0,0,0.18);
    position: relative;
    overflow: hidden;
  }
  .card--front {
    background: var(--card-dark);
    display: flex;
    align-items: center;
    justify-content: center;
  }
  .wordmark {
    display: flex;
    align-items: center;
    font-weight: 600;
    letter-spacing: -0.02em;
    line-height: 1;
  }
  .wordmark__dot {
    border-radius: 50%;
    background: var(--brand-blue);
    flex: none;
  }
  .card--front .wordmark { color: var(--card-light); font-size: 104px; gap: 22px; }
  .card--front .wordmark__dot { width: 62px; height: 62px; }

  .card--back {
    background: var(--card-light);
    display: flex;
    align-items: center;
  }
  .card--back .brand {
    width: 330px;
    display: flex;
    justify-content: center;
    padding-top: 70px;
  }
  .card--back .wordmark { color: var(--ink); font-size: 54px; gap: 12px; }
  .card--back .wordmark__dot { width: 34px; height: 34px; }
  .divider {
    width: 1.5px;
    height: 150px;
    background: var(--rule);
    margin-top: 30px;
  }
  .contact {
    padding-left: 30px;
    color: var(--ink);
  }
  .contact__name {
    font-weight: 700;
    font-size: 22px;
    line-height: 1.1;
  }
  .contact__role {
    color: var(--brand-blue);
    font-size: 17px;
    margin-bottom: 12px;
  }
  .contact__list { list-style: none; font-size: 15px; }
  .contact__list li {
    display: flex;
    align-items: center;
    gap: 10px;
    line-height: 1.75;
  }
  .contact__list svg { width: 16px; height: 16px; flex: none; }
</style>
</head>
<body>
<main class="sheet">
  <section class="card card--front" aria-label="Card front">
    <div class="wordmark"><span class="wordmark__dot"></span><span>nectara</span></div>
  </section>

  <section class="card card--back" aria-label="Card back">
    <div class="brand">
      <div class="wordmark"><span class="wordmark__dot"></span><span>nectara</span></div>
    </div>
    <div class="divider"></div>
    <div class="contact">
      <p class="contact__name">Nectara.One</p>
      <p class="contact__role">Founder/ CEO</p>
      <ul class="contact__list">
        <li>
          <svg viewBox="0 0 16 16" aria-hidden="true"><path fill="var(--brand-green)" d="M4.2 1.5l2 2.6-1.2 1.6c.8 1.8 2.3 3.3 4.1 4.1l1.6-1.2 2.6 2-1.1 2.4C7 12.5 3.5 9 2 3.8z"/></svg>
          <span>555-214-0387</span>
        </li>
        <li>
          <svg viewBox="0 0 16 16" aria-hidden="true"><rect x="1" y="3.5" width="14" height="9" rx="1" fill="var(--brand-yellow)"/><path d="M1.5 4l6.5 5 6.5-5" fill="none" stroke="#fff" stroke-width="1.2"/></svg>
          <span>dana.reeve@nectara.one</span>
        </li>
        <li>
          <svg viewBox="0 0 16 16" aria-hidden="true"><circle cx="8" cy="8" r="6.5" fill="var(--brand-red)"/><path d="M1.5 8h13M8 1.5c-2.5 3-2.5 10 0 13M8 1.5c2.5 3 2.5 10 0 13" fill="none" stroke="#fff" stroke-width="1"/></svg>
          <span>www.nectara.one</span>
        </li>
      </ul>
    </div>
  </section>
</main>
</body>
</html>
```